Need Business Card for our Real Estate Business with Sales Executive's Picture

PANTONE 484 C ( RED)

PANTONE 2766 C ( BLUE

Industry/Entity Type

Real Estate

Contact Information for Business Card

Name, Mobile, email, & picture of Person
Agency Phone, address, Web address

Requirements
Must have
• Our Logo Colours, Agent Picture,

```html
<!DOCTYPE html>
<html lang="en">
<head>
<meta charset="utf-8">
<title>Corvana Real Estate – Business Card</title>
<link rel="stylesheet" href="https://fonts.googleapis.com/css2?family=Cinzel:wght@500&family=Work+Sans:wght@400;600&display=swap">
<style>
  :root {
    --navy: #0c1a4a;
    --navy-deep: #0a1540;
    --red: #7a1424;
    --white: #ffffff;
    --grey-text: #6b6f7a;
    --page: #e6e7ea;
    --suit-light: #3a5fb8;
    --suit-dark: #1c2f6e;
  }
  * { margin: 0; padding: 0; box-sizing: border-box; }
  html, body { width: 1200px; height: 900px; overflow: hidden; background: var(--page); }
  .canvas {
    position: relative; width: 1200px; height: 900px;
    font-family: "Work Sans", sans-serif;
  }
  .card {
    position: absolute; left: 250px; width: 700px; height: 400px;
    overflow: hidden; box-shadow: 0 10px 30px rgba(0,0,0,.18);
  }
  .card--back { top: 35px; background: var(--navy); }
  .card--front { top: 465px; background: var(--white); }

  .back-brand {
    position: absolute; inset: 0;
    display: flex; align-items: center; justify-content: center; gap: 16px;
  }
  .back-brand__mark { width: 14px; height: 14px; background: var(--white); }
  .back-brand__name {
    font-family: "Cinzel", serif; font-weight: 500; font-size: 64px;
    letter-spacing: 8px; color: var(--white);
  }

  .agent-photo {
    position: absolute; left: 0; top: 40px; width: 300px; height: 290px;
    background: linear-gradient(160deg, var(--suit-light) 0%, var(--suit-dark) 100%);
  }
  .front-shapes { position: absolute; inset: 0; }

  .front-brand {
    position: absolute; right: 40px; top: 95px;
    font-family: "Cinzel", serif; font-weight: 500; font-size: 54px;
    letter-spacing: 6px; color: var(--navy);
  }
  .brand-rule {
    position: absolute; right: 40px; top: 168px; width: 300px; height: 1px; background: var(--navy);
  }
  .agent {
    position: absolute; right: 60px; top: 182px; text-align: right;
  }
  .agent__name { font-weight: 600; font-size: 25px; color: var(--navy); letter-spacing: .5px; }
  .agent__title { font-size: 16px; color: var(--grey-text); margin-top: 2px; }
  .accent-bars { position: absolute; right: 20px; top: 186px; display: flex; gap: 4px; }
  .accent-bars span { display: block; width: 4px; height: 40px; background: var(--red); }
  .accent-bars span + span { width: 14px; background: var(--navy); }

  .contacts {
    position: absolute; right: 40px; top: 246px; list-style: none; text-align: right;
  }
  .contacts li {
    display: flex; justify-content: flex-end; align-items: center; gap: 10px;
    font-size: 15px; color: var(--navy); line-height: 21px;
  }
  .contacts svg { width: 12px; height: 12px; fill: none; stroke: var(--navy); stroke-width: 2; }
  .address {
    position: absolute; right: 40px; bottom: 12px; text-align: right;
    font-size: 17px; line-height: 22px; color: var(--white);
  }
</style>
</head>
<body>
<main class="canvas">
  <section class="card card--back" aria-label="Card back">
    <div class="back-brand">
      <span class="back-brand__mark"></span>
      <span class="back-brand__name">CORVANA</span>
    </div>
  </section>

  <section class="card card--front" aria-label="Card front">
    <div class="agent-photo" role="img" aria-label="Portrait photo of the agent in a blue suit and striped tie"></div>
    <svg class="front-shapes" viewBox="0 0 700 400" width="700" height="400" aria-hidden="true">
      <path d="M0 330 C 200 300 330 315 460 345 L700 345 L700 400 L0 400 Z" fill="var(--navy)"/>
      <path d="M120 300 C 260 292 360 300 470 340 C 350 308 250 304 120 308 Z" fill="var(--red)"/>
    </svg>

    <div class="front-brand">CORVANA</div>
    <div class="brand-rule"></div>

    <div class="agent">
      <div class="agent__name">DANIEL HART</div>
      <div class="agent__title">Managing Director</div>
    </div>
    <div class="accent-bars"><span></span><span></span></div>

    <ul class="contacts">
      <li>+852 2100 0455
        <svg viewBox="0 0 12 12"><path d="M2 1h3l1 3-2 1a6 6 0 0 0 3 3l1-2 3 1v3a1 1 0 0 1-1 1A10 10 0 0 1 1 2a1 1 0 0 1 1-1z"/></svg></li>
      <li>+852 2100 0466
        <svg viewBox="0 0 12 12"><rect x="3" y="1" width="6" height="3"/><rect x="1" y="4" width="10" height="5"/><rect x="3" y="8" width="6" height="3"/></svg></li>
      <li>info@corvanahomes.com
        <svg viewBox="0 0 12 12"><rect x="1" y="2.5" width="10" height="7"/><path d="M1 2.5l5 4 5-4"/></svg></li>
      <li>www.corvanahomes.com
        <svg viewBox="0 0 12 12"><circle cx="6" cy="6" r="5"/><path d="M1 6h10M6 1c-2.5 3-2.5 7 0 10M6 1c2.5 3 2.5 7 0 10"/></svg></li>
    </ul>

    <address class="address" style="font-style:normal">
      Via dei Tigli, 48.<br>10100 Lorenzo (TO)
    </address>
  </section>
</main>
</body>
</html>
```